Accounting firm needing business card / letterhead designed
Marcus L. Trenholm, CPA
marcus@veltrowledger.com
www.veltrowledger.com
842 E Alder Ave Perrysburg, OH 43827
419-562-0974

```html
<!DOCTYPE html>
<html lang="en">
<head>
<meta charset="utf-8">
<title>Veltrow Ledger – Business Card</title>
<link href="https://fonts.googleapis.com/css2?family=Fira+Sans:wght@400;600&family=Fira+Sans+Condensed:wght@600&display=swap" rel="stylesheet">
<style>
  :root {
    --navy: #20124d;
    --green: #5fb52a;
    --white: #ffffff;
    --paper: #f7f7f5;
    --backdrop: #e6e6e6;
  }
  * { margin: 0; padding: 0; box-sizing: border-box; }
  html, body { width: 1200px; height: 576px; overflow: hidden; }
  body {
    background: var(--backdrop);
    position: relative;
    font-family: "Fira Sans", sans-serif;
  }
  .card {
    position: absolute;
    top: 139px;
    width: 484px;
    height: 290px;
    border-radius: 14px;
    overflow: hidden;
  }
  .card-back {
    left: 82px;
    background: var(--navy);
    display: flex;
    align-items: center;
    justify-content: center;
  }
  .card-front { left: 600px; background: var(--paper); }
  .brand-name {
    font-family: "Fira Sans", sans-serif;
    font-weight: 600;
    letter-spacing: 2px;
    text-transform: uppercase;
    white-space: nowrap;
  }
  .card-back .brand-name { color: var(--white); font-size: 40px; }
  .card-front .brand-name {
    position: absolute; left: 30px; top: 48px;
    color: var(--navy); font-size: 38px;
  }
  .wave { position: absolute; left: 0; top: 0; }
  .person { position: absolute; left: 27px; top: 150px; }
  .person-name {
    font-family: "Fira Sans Condensed", sans-serif;
    font-weight: 600; font-size: 19px; color: var(--navy);
  }
  .person-role { font-size: 12px; color: var(--green); margin-top: 3px; }
  .contact {
    position: absolute; right: 18px; top: 196px;
    list-style: none; text-align: right;
    color: var(--white); font-size: 11.5px;
  }
  .contact li {
    display: flex; align-items: center; justify-content: flex-end;
    gap: 8px; height: 18.5px;
  }
  .contact svg { width: 10px; height: 10px; fill: var(--green); }
  .contact .address { margin-top: 4px; margin-right: 0; }
</style>
</head>
<body>
  <section class="card card-back">
    <div class="brand-name">Veltrow Ledger</div>
  </section>

  <section class="card card-front">
    <div class="brand-name">Veltrow Ledger</div>

    <svg class="wave" width="484" height="290" viewBox="0 0 484 290" aria-hidden="true">
      <path d="M0,250 C120,278 250,272 335,222 C405,178 445,154 484,146 L484,290 L0,290 Z" fill="var(--navy)"/>
      <path d="M0,222 C110,256 235,258 325,207 C395,167 440,146 484,136 L484,143 C442,151 402,174 333,214 C250,262 120,262 0,238 Z" fill="var(--green)"/>
      <path d="M30,225 C120,245 220,248 300,218 C220,240 120,238 30,225 Z" fill="var(--green)"/>
    </svg>

    <div class="person">
      <div class="person-name">Marcus L. Trenholm, CPA</div>
      <div class="person-role">Director</div>
    </div>

    <ul class="contact">
      <li>419-562-0974
        <svg viewBox="0 0 10 10"><path d="M2,1 L4,1 L4.6,3 L3.4,3.8 C4,5 5,6 6.2,6.6 L7,5.4 L9,6 L9,8 C9,8.6 8.6,9 8,9 C4.2,9 1,5.8 1,2 C1,1.4 1.4,1 2,1 Z"/></svg>
      </li>
      <li>www.veltrowledger.com
        <svg viewBox="0 0 10 10"><path d="M0.5,2 L9.5,2 L9.5,8 L0.5,8 Z M1.2,2.6 L5,5.4 L8.8,2.6" stroke="var(--navy)" stroke-width="0.6"/></svg>
      </li>
      <li>marcus@veltrowledger.com
        <svg viewBox="0 0 10 10"><circle cx="5" cy="5" r="4.5"/><path d="M0.5,5 L9.5,5 M5,0.5 C3,3 3,7 5,9.5 M5,0.5 C7,3 7,7 5,9.5" stroke="var(--navy)" stroke-width="0.6" fill="none"/></svg>
      </li>
      <li class="address">842 E Alder Ave Perrysburg, OH 43827</li>
    </ul>
  </section>
</body>
</html>
```